New Website for World Wide Charity (KOLVAN)

We need a dynamic web design for our brand new charity organisation that will be working worldwide. We will be funded by donations so need to attract people to donate.

What We Do
We work to optimise the wellbeing of the planet, the animals and all that live within. Our slogan is Achieving Vibrational Equilibrium.

We have included a Powerpoint document which may help you understand what we need, it is just an idea for structure and style, it is not set in stone so feel free to be as creative as you like!
Updates

Designs look the same

Target Market(s)

Adults 18+ with an interest in animal, environmental. Businesses that may like to support our natural world or already support our natural world.

Number of Pages Required

3 page

Colors

Designer to choose colors to be used in the design.

Requirements
Must have
• We need the website to be easy to use and understand.

Web pages will be Home, What We Do, Who We Are, Success Stories, What You Can Do (Blog section), Seek Help, Donate, Join.
Nice to have
• Natural feel, easy to navigate, Ideally the website will look natural and organic.

Natural colours, blues, greens, sand, gold, brown, grey, silver, Orange and yellow for impact.
Should not have
• Should not have a dark coloured theme.

```html
<!DOCTYPE html>
<html lang="en">
<head>
<meta charset="utf-8">
<title>KOLVAN – Help Raise World Vibration</title>
<link rel="stylesheet" href="https://fonts.googleapis.com/css2?family=Archivo+Black&family=Rubik:wght@400;500&family=Roboto:wght@400&display=swap">
<style>
:root{
  --teal:#2f8a84;
  --teal-soft:#4f9d98;
  --forest:#1d6a58;
  --forest-deep:#17574a;
  --navy:#070d22;
  --ink:#333a3a;
  --line:#3a7e73;
  --white:#ffffff;
  --footer-text:#c9ced8;
  --footer-muted:#8a91a3;
}
*{box-sizing:border-box;margin:0;padding:0}
html,body{width:1200px;height:3083px;overflow:hidden}
body{position:relative;background:var(--white);font-family:"Rubik",sans-serif;color:var(--ink)}

.hero{position:absolute;left:0;top:0;width:1200px;height:640px;
  background:radial-gradient(ellipse at 70% 40%,#c9a35a 0%,#8a7a3a 12%,transparent 30%),
             radial-gradient(ellipse at 72% 55%,#c8987c 0%,transparent 35%),
             linear-gradient(180deg,#5d7a28 0%,#8aa43c 35%,#4f7022 70%,#2e4a18 100%)}
.navbar{position:absolute;left:0;top:45px;width:1200px;height:52px;background:var(--white);
  border:1px solid var(--forest);display:flex;justify-content:flex-end;align-items:center;padding-right:110px;gap:33px}
.navbar a{font-family:"Roboto",sans-serif;font-size:14px;color:#3b3b3b;text-decoration:none;letter-spacing:.2px}
.navbar a.current{color:var(--teal)}
.brand{position:absolute;left:107px;top:5px;width:132px;height:132px;border-radius:50%;
  background:var(--white);border:4px solid var(--forest);display:flex;align-items:center;justify-content:center;
  font-family:"Rubik",sans-serif;font-weight:500;font-size:20px;color:var(--forest);letter-spacing:1px}
.hero-title{position:absolute;left:110px;top:246px;font-family:"Archivo Black",sans-serif;font-size:53px;
  line-height:60px;color:var(--white);letter-spacing:1px}
.hero-cta{position:absolute;left:112px;top:443px;width:245px;height:57px;border-radius:29px;
  background:var(--teal);border:2px solid #e8f0d8;color:var(--white);font-family:"Rubik",sans-serif;
  font-weight:500;font-size:16px;display:flex;align-items:center;justify-content:center;letter-spacing:.5px}

.tiles{position:absolute;left:0;top:640px;width:1200px;height:343px;display:flex}
.tile{width:400px;height:343px;position:relative;color:var(--white);text-align:center}
.tile.environment{background:linear-gradient(135deg,#2a7a5e,#1f6a55)}
.tile.animal{background:linear-gradient(135deg,#5aa39c,#4e9791)}
.tile.human{background:linear-gradient(135deg,#1f6a58,#256f5c)}
.tile h2{position:absolute;left:0;right:0;top:150px;font-weight:400;font-size:40px;letter-spacing:1.5px}
.tile a{position:absolute;left:0;right:0;top:305px;color:var(--white);font-weight:500;font-size:16px;letter-spacing:.3px;text-decoration:underline}

.feature{position:absolute;left:135px;width:928px;height:456px;border:1px solid var(--line);background:var(--white)}
.feature .photo{position:absolute;top:14px;width:422px;height:427px;display:flex;align-items:flex-end;justify-content:center;padding-bottom:16px}
.feature .photo span{color:var(--white);font-size:40px;letter-spacing:1px}
.feature p{position:absolute;top:76px;width:380px;font-size:17.5px;line-height:27.5px;color:var(--ink)}
.feature.left .photo{left:17px}
.feature.left p{left:481px}
.feature.right .photo{right:17px}
.feature.right p{left:62px}
.photo.soil{background:linear-gradient(180deg,#6f8a3a 0%,#7a5a3c 45%,#3b2a1e 85%,#111 100%)}
.photo.bear{background:linear-gradient(180deg,#8a8a70 0%,#6a5a44 40%,#4a3626 75%,#1a1208 100%)}
.photo.person{background:linear-gradient(180deg,#3a5a34 0%,#2e4a2a 40%,#5a6a8a 70%,#141a18 100%)}

.footer{position:absolute;left:0;top:2650px;width:1200px;height:433px}
.footer svg{position:absolute;left:0;top:0}
.footer-brand{position:absolute;left:112px;top:120px;width:172px;height:172px;border-radius:50%;
  border:4px solid #3b5fa8;display:flex;align-items:center;justify-content:center;
  font-family:"Rubik",sans-serif;font-weight:500;font-size:26px;color:#3b8f99;letter-spacing:1.5px}
.footer-col{position:absolute;top:130px}
.footer-col h3{font-weight:500;font-size:21px;color:var(--teal);margin-bottom:20px}
.footer-col li{list-style:none;font-size:16px;color:var(--footer-text);line-height:27.5px}
.footer-rule{position:absolute;left:110px;top:347px;width:979px;height:1px;background:#2a3048}
.footer-small{position:absolute;top:380px;font-size:15px;color:var(--footer-muted)}
</style>
</head>
<body>

<header class="hero" role="img" aria-label="Cupped hands holding a glass globe above green grass">
  <nav class="navbar">
    <a class="current">HOME</a>
    <a>WHAT WE DO</a>
    <a>WHO WE ARE</a>
    <a>SUCCESS STORIES</a>
    <a>WHAT YOU CAN DO</a>
    <a>DONATE AND JOIN</a>
  </nav>
  <div class="brand">KOLVAN</div>
  <h1 class="hero-title">HELP RAISE<br>WORLD<br>VIBRATION</h1>
  <div class="hero-cta">MAKE A DIFFERENCE</div>
</header>

<section class="tiles">
  <div class="tile environment" role="img" aria-label="Smiling woman in a recycling t-shirt, tinted green">
    <h2>ENVIRONMENT</h2><a>FIND OUT MORE</a>
  </div>
  <div class="tile animal" role="img" aria-label="Bear sitting on rocks, tinted teal">
    <h2>ANIMAL</h2><a>FIND OUT MORE</a>
  </div>
  <div class="tile human" role="img" aria-label="Hand holding a seedling, tinted green">
    <h2>HUMAN</h2><a>FIND OUT MORE</a>
  </div>
</section>

<article class="feature left" style="top:1095px">
  <div class="photo soil" role="img" aria-label="Several hands holding soil with green seedlings"><span>ENVIRONMENT</span></div>
  <p>Sed ut perspiciatis unde omnis iste natus error sit voluptatem accusantium doloremque laudantium, totam rem aperiam, eaque ipsa quae ab illo inventore veritatis et quasi architecto beatae vitae dicta sunt explicabo. Nemo enim ipsam voluptatem quia voluptas sit aspernatur aut odit aut fugit, sed quia consequuntur magni dolores eos qui ratione voluptatem sequi nesciunt. Neque porro quisquam est, qui dolorem ipsum quia dolor sit</p>
</article>

<article class="feature right" style="top:1601px">
  <p>Sed ut perspiciatis unde omnis iste natus error sit voluptatem accusantium doloremque laudantium, totam rem aperiam, eaque ipsa quae ab illo inventore veritatis et quasi architecto beatae vitae dicta sunt explicabo. Nemo enim ipsam voluptatem quia voluptas sit aspernatur aut odit aut fugit, sed quia consequuntur magni dolores eos qui ratione voluptatem sequi nesciunt. Neque porro quisquam est, qui dolorem ipsum quia dolor sit</p>
  <div class="photo bear" role="img" aria-label="Brown bear standing in a forest"><span>ANIMAL</span></div>
</article>

<article class="feature left" style="top:2108px">
  <div class="photo person" role="img" aria-label="Young woman with a butterfly on her hand among greenery"><span>HUMAN</span></div>
  <p>Sed ut perspiciatis unde omnis iste natus error sit voluptatem accusantium doloremque laudantium, totam rem aperiam, eaque ipsa quae ab illo inventore veritatis et quasi architecto beatae vitae dicta sunt explicabo. Nemo enim ipsam voluptatem quia voluptas sit aspernatur aut odit aut fugit, sed quia consequuntur magni dolores eos qui ratione voluptatem sequi nesciunt. Neque porro quisquam est, qui dolorem ipsum quia dolor sit</p>
</article>

<footer class="footer">
  <svg width="1200" height="433" viewBox="0 0 1200 433">
    <path d="M111 50 Q600 -25 1089 50 L1089 62 Q600 -5 111 62 Z" fill="var(--teal)"/>
    <path d="M0 66 Q600 -20 1200 66 L1200 433 L0 433 Z" fill="var(--navy)"/>
  </svg>
  <div class="footer-brand">KOLVAN</div>
  <div class="footer-col" style="left:430px">
    <h3>Get Involved</h3>
    <ul><li>Join Us</li><li>Fundraise</li><li>Donate</li><li>Shop</li></ul>
  </div>
  <div class="footer-col" style="left:696px">
    <h3>Get Help</h3>
    <ul><li>Contact Us</li><li>Media</li></ul>
  </div>
  <div class="footer-col" style="left:924px">
    <h3>Legal</h3>
    <ul><li>Terms and Conditions</li><li>Cookies</li><li>Privacy Policy</li></ul>
  </div>
  <div class="footer-rule"></div>
  <div class="footer-small" style="left:110px">Copyright © 2021.&nbsp; All rights reserved</div>
  <div class="footer-small" style="right:111px">Charity Number: 1048276</div>
</footer>

</body>
</html>
```